Envelope Design - Winner can do follow-up business

- Varnoko.com is a Swiss-based online store selling business shirts and accessories for business men
- Please visit the webpage to make yourself familiar with the company. Although the text is in German, with Plimbo translator you should be able to understand the main content.
- Our clients are mainly business men between 30 and 60 years old. Mostly with a high income working in the service industry (banking, insurance, lawyers, etc.). Sometimes there wives purchase the shirts for them ;-)
- The colors and the logo are given, as they are also used for the print materials (please see files in attachment)
- I am running several businesses and often need a talented web designer --> the winner gets substantial follow-up business
your task:
-for our company we need a new envelope design
-It should be simple and modern
-please use one of the logos in the followings.
-suprise me :)

```html
<!DOCTYPE html>
<html lang="en">
<head>
<meta charset="utf-8">
<title>Varnoko Envelope</title>
<link rel="stylesheet" href="https://fonts.googleapis.com/css2?family=Lexend+Exa:wght@500&family=Open+Sans:wght@400&display=swap">
<style>
  :root {
    --backdrop: #ecebe8;
    --paper: #ffffff;
    --edge: #3a3a3a;
    --brand-yellow: #e8d66a;
    --brand-red: #ee3124;
    --ink: #1d1d1d;
  }
  * { margin: 0; padding: 0; box-sizing: border-box; }
  html, body { width: 1200px; height: 962px; overflow: hidden; }
  body { background: var(--backdrop); position: relative; font-family: "Open Sans", sans-serif; }

  .envelope { position: absolute; background: var(--paper); }
  .envelope-back-branded { left: 150px; top: 70px; width: 974px; height: 400px; }
  .envelope-back-plain { left: 58px; top: 240px; width: 974px; height: 460px; border: 1px solid var(--edge); }
  .envelope-front { left: 157px; top: 425px; width: 975px; height: 460px; border: 1px solid var(--edge); border-bottom: none; }

  .flap { position: absolute; left: 0; top: 0; display: block; }

  .flap-name {
    position: absolute; left: 0; right: 0; top: 42px;
    text-align: center;
    font-family: "Lexend Exa", sans-serif; font-weight: 500;
    font-size: 40px; letter-spacing: 1px;
    color: var(--brand-red);
  }

  .brand-block { position: absolute; left: 30px; top: 30px; width: 280px; }
  .brand-square {
    display: block; width: 44px; height: 44px; margin-left: 116px;
    background: var(--brand-red);
  }
  .brand-name {
    margin-top: 22px;
    font-family: "Lexend Exa", sans-serif; font-weight: 500;
    font-size: 44px; letter-spacing: 1px; line-height: 1;
    color: var(--brand-yellow);
  }

  .contact { position: absolute; top: 390px; display: flex; align-items: center; gap: 10px; font-size: 20px; color: var(--ink); }
  .contact-address { left: 28px; }
  .contact-web { right: 26px; }

  .stripe { position: absolute; left: 0; right: 0; }
  .stripe-yellow { top: 434px; height: 8px; background: var(--brand-yellow); }
  .stripe-red { top: 445px; height: 15px; background: var(--brand-red); }
</style>
</head>
<body>

  <div class="envelope envelope-back-branded">
    <svg class="flap" width="974" height="160" viewBox="0 0 974 160" aria-hidden="true">
      <path d="M0 0 H974 C966 40 960 70 880 88 L520 150 C500 154 474 154 454 150 L94 88 C14 70 8 40 0 0 Z" fill="var(--brand-yellow)"/>
    </svg>
    <div class="flap-name">VARNOKO</div>
  </div>

  <div class="envelope envelope-back-plain">
    <svg class="flap" width="974" height="160" viewBox="0 0 974 160" aria-hidden="true">
      <path d="M0 0 C10 40 16 70 96 86 L440 150 C460 155 494 155 514 150 L858 86 C938 70 944 40 974 0" fill="none" stroke="var(--edge)" stroke-width="1"/>
    </svg>
  </div>

  <div class="envelope envelope-front">
    <div class="brand-block">
      <span class="brand-square"></span>
      <div class="brand-name">VARNOKO</div>
    </div>

    <div class="contact contact-address">
      <svg width="18" height="24" viewBox="0 0 18 24" aria-hidden="true">
        <path d="M9 0C4 0 0 4 0 9c0 6 9 15 9 15s9-9 9-15c0-5-4-9-9-9z" fill="var(--brand-red)"/>
        <circle cx="9" cy="9" r="3.5" fill="var(--paper)"/>
      </svg>
      <span>Street Name, City Name, State Zipcode</span>
    </div>

    <div class="contact contact-web">
      <svg width="24" height="24" viewBox="0 0 24 24" fill="none" stroke="var(--brand-red)" stroke-width="1.4" aria-hidden="true">
        <circle cx="12" cy="12" r="10.5"/>
        <ellipse cx="12" cy="12" rx="4.5" ry="10.5"/>
        <line x1="1.5" y1="12" x2="22.5" y2="12"/>
        <path d="M3.5 6.5h17M3.5 17.5h17"/>
      </svg>
      <span>www.varnoko.com</span>
    </div>

    <div class="stripe stripe-yellow"></div>
    <div class="stripe stripe-red"></div>
  </div>

</body>
</html>
```